Graphic Design Project

We make rose petal jelly from old fashioned english roses. The jelly is sweet eaten with scones and clotted cream or as a filling in a victoria sandwich, as a topping on ice cream or thick set yogurt.
The image of the product is luxurious and decadent and very english.
We need a design for a label which has a picture of an old fashioned rose (rosa mundi or a compte de chambard) The rose must stand out clearly so the jelly is not confused with other fruit jams. The overall colour of the label should be pink and soft, with white or dark pink writing. The label needs to be fridge proof.

We also need a security strip to fit on the lid of the jar.

We need the following information on the label.
Name of our company-"Meadow Crown"
Name of Product-"Rose Petal Jelly"
Sales pitch-"With whole petals-a taste of summer, delicious on scones, as a filling in sponge cake, as a topping on ice cream or yogurt."
INGREDIENTS: Sugar, water, rose petals, lemon juice, natural jelling agent (agar-agar)
STORAGE: Store in a cool dry place, once opened keep refrigerated and consume within 4 weeks.
BEST BEFORE: See base

200g
Produced by:
MEADOW CROWN
The Larches
Pardew Lane
Ashcombe
Marlowshire
GL17 4RX
The label must have room for a bar code. The size of label approx 8-10cm long 5cm wide.
Updates

Hi

Just been looking at the Hartwell and Brace site and the labels they have there have the up market feel I am trying to convey. Hope that helps, its classy but not twee.

Thanks

Thanks for all submissions. I would be grateful if you googled images for 'Colourful and expensive biscuits at Hartwell Brace' The designs on the tins are the image we are trying to create. The colours are quite strong.

Thanks

Target Market(s)

older well off people who visit garden centres

Industry/Entity Type

Security

Requirements
Must have
• All writen info above and picture of old fashioned rose prferably rose a mundi. Luxury feel, very english, to appeal to older market
Pink colour sheme
Should not have
• dark or manly colours

```html
<!DOCTYPE html>
<html lang="en">
<head>
<meta charset="utf-8">
<title>Meadow Crown Rose Petal Jelly Label</title>
<link href="https://fonts.googleapis.com/css2?family=Sorts+Mill+Goudy&display=swap" rel="stylesheet">
<style>
  :root {
    --berry: #86093f;
    --petal-pink: #f5a3d3;
    --label-white: #ffffff;
    --ink: #111111;
    --rose-red: #d0102a;
    --rose-deep: #7a0015;
  }
  html, body {
    margin: 0;
    padding: 0;
    width: 1200px;
    height: 750px;
    overflow: hidden;
    background: var(--label-white);
  }
  .label {
    position: relative;
    width: 1200px;
    height: 750px;
    font-family: "Sorts Mill Goudy", "Goudy Old Style", Georgia, serif;
    font-variant-numeric: oldstyle-nums;
    overflow: hidden;
  }
  .front-panel {
    position: absolute;
    left: 0;
    top: 0;
    width: 797px;
    height: 750px;
    background: var(--berry);
    color: var(--label-white);
  }
  .front-panel p {
    position: absolute;
    margin: 0;
    line-height: 1;
    white-space: nowrap;
  }
  .company-name {
    left: 0; width: 810px; text-align: center;
    top: 44px; font-size: 52px;
  }
  .product-name {
    left: 0; width: 828px; text-align: center;
    top: 112px; font-size: 74px; color: var(--petal-pink);
  }
  .tagline {
    left: 0; width: 812px; text-align: center;
    top: 202px; font-size: 26px;
  }
  .rose-artwork {
    position: absolute;
    left: 272px;
    top: 290px;
    width: 270px;
    height: 228px;
  }
  .front-panel .serving-ideas {
    left: 0; width: 828px; text-align: center;
    top: 582px; font-size: 31.5px; line-height: 39px;
    white-space: normal;
  }
  .net-weight {
    left: 585px; top: 693px; font-size: 40px;
  }
  .info-panel {
    position: absolute;
    left: 818px;
    top: 0;
    width: 382px;
    height: 750px;
    color: var(--ink);
  }
  .info-block {
    position: absolute;
    left: 0;
    margin: 0;
    font-size: 23.5px;
    line-height: 30px;
    white-space: nowrap;
  }
  .ingredients { top: 26px; }
  .storage { top: 148px; }
  .best-before { top: 277px; }
  .producer {
    top: 379px;
    font-size: 28px;
    line-height: 35px;
  }
  .barcode-space {
    position: absolute;
    left: 1001px;
    top: 635px;
    width: 175px;
    height: 91px;
    border: 1.5px solid var(--ink);
    box-sizing: border-box;
    padding: 22px 0 0 6px;
    font-family: Arial, Helvetica, sans-serif;
    font-size: 17px;
    line-height: 24px;
    color: var(--ink);
  }
</style>
</head>
<body>
<main class="label">
  <section class="front-panel">
    <p class="company-name">Meadow Crown</p>
    <p class="product-name">Rose Petal Jelly</p>
    <p class="tagline">"With whole petals its a taste of summer”</p>

    <svg class="rose-artwork" viewBox="0 0 270 228" role="img" aria-label="Three red old fashioned roses with white outlines">
      <defs>
        <radialGradient id="rose-tone" cx="50%" cy="50%" r="60%">
          <stop offset="0%" stop-color="#7a0015"/>
          <stop offset="55%" stop-color="#d0102a"/>
          <stop offset="100%" stop-color="#e83a52"/>
        </radialGradient>
      </defs>
      <rect x="0" y="0" width="270" height="228" rx="100" fill="url(#rose-tone)"/>
    </svg>

    <p class="serving-ideas">Delicious on scones, as a filling<br>in sponge cake, as a topping<br>on ice cream or yogurt.</p>
    <p class="net-weight">200g</p>
  </section>

  <section class="info-panel">
    <p class="info-block ingredients">INGREDIENTS:<br>Sugar, water, rose petals, lemon<br>juice, natural jelling agent (agar-agar)</p>
    <p class="info-block storage">STORAGE: Store in a cool dry<br>place, once opened keep refrigerated<br>and consume within 4 weeks.</p>
    <p class="info-block best-before">BEST BEFORE:<br>See base</p>
    <p class="info-block producer">Produced by:<br>MEADOW CROWN<br>The Larches<br>Pardew Lane<br>Ashcombe<br>Marlowshire<br>GL17 4RX</p>
  </section>

  <div class="barcode-space">Bar<br>Code</div>
</main>
</body>
</html>
```